AMBER AND SLATE WEB

We need a home design in wordpress, we have now a web but we would like to improve it. Our current web is www.amberandslatevillas.example Our business is holliday rental of villas in Ibiza. Our guest must know that we are a reliable company, professional and with experience and good reviews. We want them to click in our reservation engine: https://bookings.amberandslatevillas.example/en/ and make reservation in our website. We would also like to say that all the properties that we have are just us who commercialize so we have best price available. Many people are going to see our villas in staylist.example and look to our website to make a reservation with us so we need to show them that they are at the right place and click at our link to our reservation engine. What make us special is that we are a local company, we are from Ibiza, Our guests are always received in person by the Amber and Slate Ibiza team. You will enjoy extensive tourist information when you check in and during the entire stay. You will be attended by ChatterLine and calls, always happy to help so that you have a happy and fun stay! Our guest stay is better than in hotel as they have more spece, private swiming pool, private garden, barbeque ... To rent a villa is the best way to stay in Ibiza. We also have a promotional video: https://vidshare.example/Qm7TzR2pLxA Let our philosophy be shown, we think that coming on holiday to Ibiza implies seeing the nature that we have in Ibiza, hence our name AMBER AND SLATE, like the pins that almost touch the sea in Ibiza, or the posidonea meadows where the intense green of the seaweed and the blue of the sea. We are aware of the environment, and we love Ibiza. For us, the client who visits Ibiza, should rent a car, go around the island, eat in a restaurant one day in front of the sea, is a night of partying to the discs, go shopping, visit the ancient heritage of Umanity, make some aquatic sport, enjoy the pool, those are for us Ibiza.

Target Market(s)

Europe, people from Holand, UK, Germany, France, Spain ...

Industry/Entity Type

Tourism

Colors

Designer to choose colors to be used in the design.

Requirements
Must have
• Pictures of Ibiza.
Nice to have
• Our name Amber and Slate Ibiza is beacuse in Ibiza there is forest that almost touch the watter of the Mediterranean sea, so you can see green of the forest and blue of the sea and the sky. And also beacause under the watter of the sea there is a plant called Posidonia that is also green please see the picture of posidonia.

```html
<!DOCTYPE html>
<html lang="en">
<head>
<meta charset="utf-8">
<title>Amber and Slate Villas Ibiza</title>
<link rel="stylesheet" href="https://fonts.googleapis.com/css2?family=Libre+Baskerville:wght@400;700&family=Roboto:wght@400;500;700&display=swap">
<style>
:root{
  --green:#8cc63f;
  --green-dark:#76b82a;
  --blue:#3a94c9;
  --blue-dark:#2f7fb2;
  --ink:#222;
  --text:#555;
  --muted:#8a8a8a;
  --dark:#1e1e1e;
  --light:#f3f3f3;
  --serif:"Libre Baskerville",Georgia,serif;
  --sans:"Roboto",Arial,sans-serif;
}
*{box-sizing:border-box;margin:0;padding:0}
html,body{width:1200px;height:4216px;overflow:hidden;background:#fff;font-family:var(--sans);color:var(--text)}
.page{position:relative;width:1200px;height:4216px;overflow:hidden}
.abs{position:absolute}
.btn{position:absolute;display:flex;align-items:center;justify-content:center;color:#fff;font:700 14px var(--sans);text-transform:uppercase;letter-spacing:.2px}
.btn-green{background:var(--green)}
.btn-blue{background:var(--blue)}
.center{left:0;width:1200px;text-align:center}
.sec-title{font:400 29px var(--serif);color:var(--ink);letter-spacing:.5px}
.sec-title b{font-weight:700}
.sec-title span{color:var(--blue)}
.rule{position:absolute;left:576px;width:48px;height:3px;background:var(--green)}

/* header */
.topline{left:0;top:0;width:1200px;height:4px;background:var(--blue)}
.logo{left:144px;top:40px;display:flex;align-items:center;gap:12px}
.logo i{width:38px;height:38px;border-radius:50%;background:var(--green);display:block}
.logo span{font:400 24px var(--serif);color:var(--green-dark);letter-spacing:.5px}
.call{left:616px;top:24px;display:flex;gap:10px;align-items:center}
.call .ic{width:30px;height:30px;border-radius:50%;background:var(--blue);display:flex;align-items:center;justify-content:center}
.call small{display:block;font:500 12px var(--sans);color:var(--ink)}
.call strong{display:block;font:500 19px var(--sans);color:var(--green-dark)}
.nav{top:84px;left:580px;display:flex;gap:32px;font:500 14px var(--sans);color:var(--ink)}
.lang{left:987px;top:77px;width:68px;height:30px;border:1px solid #ccc;font:500 10px var(--sans);color:#333;display:flex;align-items:center;justify-content:center;gap:5px}
.lang i{width:12px;height:8px;background:#c9d3e4;display:block}

/* hero */
.hero{left:0;top:103px;width:1200px;height:516px;background:linear-gradient(180deg,#3f7dc4 0%,#6fa6d8 22%,#2e6b3f 45%,#1b95b8 70%,#42c0c8 100%)}
.hero-title{top:360px;font:700 56px/76px var(--serif);color:#fff;text-shadow:0 3px 8px rgba(0,0,0,.45);text-transform:uppercase}
.arrow{position:absolute;width:32px;height:32px;border-radius:50%;background:rgba(0,0,0,.55);display:flex;align-items:center;justify-content:center}
.dots{top:570px;left:562px;display:flex;gap:8px}
.dots i{width:9px;height:9px;border-radius:50%;background:#fff;display:block}
.dots i.off{background:transparent;border:2px solid #fff}

/* booking */
.booking{left:0;top:619px;width:1200px;height:82px;background:var(--dark)}
.field{position:absolute;top:21px;height:38px;background:#fff;font:400 12px var(--sans);color:#444;display:flex;align-items:center;justify-content:space-between;padding:0 14px 0 16px}

/* intro */
.intro{left:0;top:701px;width:1200px;height:780px;background:linear-gradient(180deg,#d6e6ef 0%,#eaf2f4 40%,#f6f7f6 70%,#f3f3f3 100%)}
.intro-title{top:913px;font:700 26px var(--serif);color:var(--ink);letter-spacing:.5px}
.intro-sub{top:960px;font:400 26px var(--serif);color:var(--blue);letter-spacing:.5px}
.intro-copy{top:1050px;left:230px;width:740px;text-align:center;font:400 14px/33px var(--sans);color:#444}
.intro-copy p+p{margin-top:32px}

/* featured */
.featured{left:0;top:1481px;width:1200px;height:591px;background:var(--light)}
.card{position:absolute;top:1642px;width:285px;height:322px;background:#fff;box-shadow:0 2px 6px rgba(0,0,0,.12)}
.card .ph{position:absolute;left:0;top:0;width:285px;height:198px}
.card .price{position:absolute;left:12px;top:170px;font:700 16px var(--sans);color:#fff}
.card .price small{font-size:10px;font-weight:400}
.card h3{position:absolute;left:20px;top:218px;font:500 15px var(--sans);color:var(--ink)}
.card p{position:absolute;left:20px;top:248px;font:400 12.5px var(--sans);color:var(--muted)}
.card .meta{position:absolute;left:0;bottom:0;width:285px;height:36px;border-top:1px solid #eee;display:flex;align-items:center;font:400 13px var(--sans);color:#444}
.card .meta span{display:flex;align-items:center;gap:6px;padding:0 9px 0 7px;border-right:1px solid #eee;height:22px}
.card .meta span:first-child{padding-left:7px}
.card .meta .more{border:0;margin-left:auto;padding-right:20px}
.ring{position:absolute;width:36px;height:36px;border-radius:50%;border:1.5px solid #777;background:#fff;display:flex;align-items:center;justify-content:center}

/* services */
.services{left:0;top:2072px;width:1200px;height:601px;background:linear-gradient(180deg,#8cc63f 0%,#7fc24c 100%)}
.svc{position:absolute;top:2263px;width:207px;height:297px;text-align:center}
.svc svg.shape{position:absolute;left:0;top:0}
.svc .pin{position:absolute;left:72px;top:40px}
.svc h4{position:absolute;left:0;width:207px;top:158px;font:500 14.5px var(--sans);color:var(--ink)}
.svc p{position:absolute;left:22px;width:163px;top:186px;font:400 11.5px/21px var(--sans);color:var(--muted)}
.svc a{position:absolute;left:0;width:207px;top:262px;font:500 11px var(--sans);color:var(--blue);text-decoration:none}
.ring-w{position:absolute;width:44px;height:44px;border-radius:50%;border:2px solid #fff;display:flex;align-items:center;justify-content:center}

/* about */
.about{left:0;top:2673px;width:1200px;height:455px;background:var(--light)}
.about-copy{left:678px;top:2808px;width:380px;font:400 14px/30px var(--sans);color:#555}
.about-title{left:678px;top:2736px;font:400 28px var(--serif);color:var(--ink)}
.about-title b{font-weight:700}
.about-title span{color:var(--blue)}

/* blog */
.post{position:absolute;top:3326px;width:437px}
.post .ph{position:absolute;left:0;top:0;width:437px;height:285px}
.post .box{position:absolute;left:70px;top:238px;width:367px;height:240px;background:#fff}
.post h3{position:absolute;left:22px;top:28px;font:500 16px var(--sans);color:var(--ink)}
.post .meta{position:absolute;left:22px;top:65px;font:400 11px var(--sans);color:#444;display:flex;gap:8px;align-items:center}
.post .meta i{display:inline-block;width:9px;height:9px;border-radius:2px;background:var(--green);margin-right:5px}
.post .txt{position:absolute;left:22px;top:94px;width:330px;font:400 11.5px/27px var(--sans);color:#777}
.post .btn{left:22px;top:212px;width:103px;height:32px;font-size:12px}

/* footer */
.footer{left:0;top:3840px;width:1200px;height:376px}
.social{top:3990px;left:403px;display:flex;gap:12px}
.social span{width:56px;height:56px;border-radius:50%;border:2px solid #fff;display:flex;align-items:center;justify-content:center}
.f-contact{top:4079px;font:400 13px var(--sans);color:#fff;display:flex;justify-content:center;gap:12px;align-items:center}
.f-nav{top:4118px;font:500 14px var(--sans);color:#fff;word-spacing:2px}
.f-copy{top:4160px;font:400 12px var(--sans);color:#fff}
</style>
</head>
<body>
<div class="page">

  <!-- header -->
  <header>
    <div class="abs topline"></div>
    <div class="abs logo"><i></i><span>AMBER AND SLATE</span></div>
    <div class="abs call">
      <div class="ic"><svg width="16" height="16" viewBox="0 0 24 24"><path fill="#fff" d="M6.6 10.8a15 15 0 0 0 6.6 6.6l2.2-2.2c.3-.3.7-.4 1-.2 1.1.4 2.3.6 3.6.6.6 0 1 .4 1 1V20c0 .6-.4 1-1 1A17 17 0 0 1 3 4c0-.6.4-1 1-1h3.5c.6 0 1 .4 1 1 0 1.3.2 2.5.6 3.6.1.3 0 .7-.2 1z"/></svg></div>
      <div><small>CALL US:</small><strong>+34600418257</strong></div>
    </div>
    <div class="btn btn-green" style="left:810px;top:27px;width:134px;height:31px;font-size:12px;font-weight:500">All Properties</div>
    <div class="btn btn-blue" style="left:955px;top:27px;width:100px;height:31px;font-size:12px;font-weight:500">Book Now</div>
    <nav class="abs nav"><span>HOME</span><span>EXPERIENCE</span><span>ABOUT US</span><span>CONTACT US</span></nav>
    <div class="abs lang"><i></i>LAN<svg width="7" height="5" viewBox="0 0 7 5"><path d="M0 0l3.5 4L7 0" fill="none" stroke="#333"/></svg></div>
  </header>

  <!-- hero -->
  <section>
    <div class="abs hero" role="img" aria-label="Photo of an Ibiza cove with pine trees meeting turquoise sea and sailboats"></div>
    <svg class="abs" style="left:0;top:100px" width="1200" height="30" viewBox="0 0 1200 30">
      <polygon points="0,0 518,0 518,3 550,25 1200,25 1200,0" fill="#fff"/>
      <polyline points="0,3 518,3 552,25 1200,25" fill="none" stroke="#2f7fb2" stroke-width="3"/>
    </svg>
    <h1 class="abs center hero-title">The best way to<br>stay in Ibiza!</h1>
    <div class="arrow" style="left:104px;top:387px"><svg width="10" height="12" viewBox="0 0 10 12"><path d="M7 1L2 6l5 5" fill="none" stroke="#fff" stroke-width="2"/></svg></div>
    <div class="arrow" style="left:1064px;top:387px"><svg width="10" height="12" viewBox="0 0 10 12"><path d="M3 1l5 5-5 5" fill="none" stroke="#fff" stroke-width="2"/></svg></div>
    <div class="abs dots"><i></i><i></i><i class="off"></i><i></i><i></i></div>
  </section>

  <!-- booking bar -->
  <section class="abs booking">
    <div class="field" style="left:166px;width:226px">Best Available rate
      <svg width="22" height="14" viewBox="0 0 22 14"><path d="M1 0v14M1 10h20v4M1 7h20v3M4 4h5v3M10 4h11v3" fill="none" stroke="#333" stroke-width="2"/></svg></div>
    <div class="field" style="left:406px;width:225px">Check in - Check out
      <svg width="14" height="14" viewBox="0 0 14 14"><rect x="1" y="2" width="12" height="11" fill="none" stroke="#333" stroke-width="1.5"/><path d="M1 5h12M4 0v3M10 0v3" stroke="#333" stroke-width="1.5"/></svg></div>
    <div class="field" style="left:646px;width:225px">2 Adults - 0 Kids
      <svg width="8" height="12" viewBox="0 0 8 12"><path d="M0 5l4-5 4 5zM0 7l4 5 4-5z" fill="#333"/></svg></div>
    <div class="btn btn-green" style="left:886px;top:21px;width:147px;height:38px;font-weight:500">Book Now</div>
  </section>

  <!-- intro -->
  <section>
    <div class="abs intro" role="img" aria-label="Faded photo of an Ibiza beach with palm trees"></div>
    <svg class="abs" style="left:0;top:1370px" width="1200" height="125" viewBox="0 0 1200 125">
      <polygon points="0,0 0,125 1200,125 1200,95" fill="#f3f3f3"/>
      <polygon points="990,117 1200,55 1200,120" fill="#2f8fc7"/>
    </svg>
    <div class="abs" style="left:567px;top:790px;width:66px;height:66px;border-radius:50%;background:var(--green-dark)"></div>
    <h2 class="abs center intro-title">VILLAS AND THE COUNTRYSIDE THE BEST</h2>
    <p class="abs center intro-sub">OPTION TO STAY IN IBIZA</p>
    <div class="rule" style="top:1011px"></div>
    <div class="abs intro-copy">
      <p>Amber and Slate Ibiza is a company specialized in offering its clients accommodation in Villas on the countryside of Ibiza. Our guests enjoy the rural Ibiza, tranquility, relax, private pool, close to dream beaches and coves, the best restaurants, an unforgettable holiday for family or friends.</p>
      <p>Every day can be a different experience, beach, restaurant, flea market, disco, hiking, kayaking, horseback riding, shopping, history, boat ride! There is a lot of variety for all budgets!</p>
    </div>
    <div class="btn btn-green" style="left:484px;top:1291px;width:231px;height:47px;font-size:15px;gap:8px">Read more info
      <svg width="14" height="14" viewBox="0 0 14 14"><circle cx="7" cy="7" r="7" fill="#fff"/><path d="M5.5 4l3 3-3 3" fill="none" stroke="#8cc63f" stroke-width="2"/></svg></div>
  </section>

  <!-- featured properties -->
  <section>
    <div class="abs featured" style="top:1495px;height:577px"></div>
    <h2 class="abs center sec-title" style="top:1545px"><b>FEATURED</b> <span>PROPERTIES</span></h2>
    <div class="rule" style="top:1594px"></div>
    <div class="ring" style="left:82px;top:1787px"><svg width="10" height="12" viewBox="0 0 10 12"><path d="M7 1L2 6l5 5" fill="none" stroke="#444" stroke-width="2"/></svg></div>
    <div class="ring" style="left:1082px;top:1787px"><svg width="10" height="12" viewBox="0 0 10 12"><path d="M3 1l5 5-5 5" fill="none" stroke="#444" stroke-width="2"/></svg></div>

    <article class="card" style="left:144px">
      <div class="ph" role="img" aria-label="Photo of a rocky islet off the Ibiza coast with boats on turquoise water" style="background:linear-gradient(180deg,#4a8fd0 0%,#6b7b6e 40%,#1f8fb0 65%,#0e6e92 100%)"></div>
      <div class="price">$45<small>/day</small></div>
      <h3>LOREM IPSUM DOLOR</h3><p>18 Olive Grove Lane, Vista Mar, IB</p>
      <div class="meta"><span><svg width="16" height="11" viewBox="0 0 16 11"><path d="M1 0v11M1 8h14v3M1 5h14v3M3 2h4v3M8 2h7v3" fill="none" stroke="#8cc63f" stroke-width="2"/></svg>2 bedrooms</span><span><svg width="14" height="12" viewBox="0 0 14 12"><path d="M0 6h14c0 3-2 5-5 5H5C2 11 0 9 0 6zM2 6V2a2 2 0 0 1 4 0" fill="#3a94c9" stroke="#3a94c9"/></svg>1 bathroom</span><span class="more"><svg width="12" height="12" viewBox="0 0 12 12"><circle cx="6" cy="6" r="6" fill="#8cc63f"/><path d="M6 3v6M3 6h6" stroke="#fff" stroke-width="1.6"/></svg></span></div>
    </article>
    <article class="card" style="left:459px">
      <div class="ph" role="img" aria-label="Photo of Ibiza old town seen from a terrace with lounge chairs" style="background:linear-gradient(180deg,#2f8fe0 0%,#dfe3e6 35%,#2aa7d0 60%,#8a8582 85%,#5f5a55 100%)"></div>
      <div class="price">$45<small>/day</small></div>
      <h3>LOREM IPSUM DOLOR</h3><p>18 Olive Grove Lane, Vista Mar, IB</p>
      <div class="meta"><span><svg width="16" height="11" viewBox="0 0 16 11"><path d="M1 0v11M1 8h14v3M1 5h14v3M3 2h4v3M8 2h7v3" fill="none" stroke="#8cc63f" stroke-width="2"/></svg>2 bedrooms</span><span><svg width="14" height="12" viewBox="0 0 14 12"><path d="M0 6h14c0 3-2 5-5 5H5C2 11 0 9 0 6zM2 6V2a2 2 0 0 1 4 0" fill="#3a94c9" stroke="#3a94c9"/></svg>1 bathroom</span><span class="more"><svg width="12" height="12" viewBox="0 0 12 12"><circle cx="6" cy="6" r="6" fill="#8cc63f"/><path d="M6 3v6M3 6h6" stroke="#fff" stroke-width="1.6"/></svg></span></div>
    </article>
    <article class="card" style="left:773px">
      <div class="ph" role="img" aria-label="Photo of Ibiza castle walls lit at dusk" style="background:linear-gradient(180deg,#1f3f8a 0%,#3e5aa8 30%,#c8782e 60%,#7a4a2a 80%,#3a3a44 100%)"></div>
      <div class="price">$45<small>/day</small></div>
      <h3>LOREM IPSUM DOLOR</h3><p>18 Olive Grove Lane, Vista Mar, IB</p>
      <div class="meta"><span><svg width="16" height="11" viewBox="0 0 16 11"><path d="M1 0v11M1 8h14v3M1 5h14v3M3 2h4v3M8 2h7v3" fill="none" stroke="#8cc63f" stroke-width="2"/></svg>2 bedrooms</span><span><svg width="14" height="12" viewBox="0 0 14 12"><path d="M0 6h14c0 3-2 5-5 5H5C2 11 0 9 0 6zM2 6V2a2 2 0 0 1 4 0" fill="#3a94c9" stroke="#3a94c9"/></svg>1 bathroom</span><span class="more"><svg width="12" height="12" viewBox="0 0 12 12"><circle cx="6" cy="6" r="6" fill="#8cc63f"/><path d="M6 3v6M3 6h6" stroke="#fff" stroke-width="1.6"/></svg></span></div>
    </article>
  </section>

  <!-- services -->
  <section>
    <div class="abs services"></div>
    <h2 class="abs center sec-title" style="top:2165px;color:#fff"><b>OUR</b> SERVICES</h2>
    <div class="rule" style="top:2212px;background:#fff"></div>
    <div class="ring-w" style="left:69px;top:2396px"><svg width="12" height="16" viewBox="0 0 12 16"><path d="M9 2L3 8l6 6" fill="none" stroke="#fff" stroke-width="2.2"/></svg></div>
    <div class="ring-w" style="left:1087px;top:2396px"><svg width="12" height="16" viewBox="0 0 12 16"><path d="M3 2l6 6-6 6" fill="none" stroke="#fff" stroke-width="2.2"/></svg></div>

    <div class="svc" style="left:144px">
      <svg class="shape" width="207" height="297" viewBox="0 0 207 297"><path d="M0 50L70 0h67l70 50v197l-70 50H70L0 247z" fill="#fff"/></svg>
      <svg class="pin" width="64" height="96" viewBox="0 0 64 96"><path d="M32 0a32 32 0 0 1 32 32c0 24-32 64-32 64S0 56 0 32A32 32 0 0 1 32 0z" fill="#3a94c9"/><circle cx="32" cy="32" r="22" fill="#fff"/><circle cx="32" cy="32" r="18" fill="#8cc63f"/><path d="M22 36v-6l3-6h14l3 6v6zM24 36v3h3v-3M37 36v3h3v-3" fill="#fff"/></svg>
      <h4>RENT A CAR</h4><p>Lorem ipsum dolor sit amet, consectetur adipiscing elit, sed do eiusmod tempor</p><a>READ MORE</a>
    </div>
    <div class="svc" style="left:379px">
      <svg class="shape" width="207" height="297" viewBox="0 0 207 297"><path d="M0 50L70 0h67l70 50v197l-70 50H70L0 247z" fill="#fff"/></svg>
      <svg class="pin" width="64" height="96" viewBox="0 0 64 96"><path d="M32 0a32 32 0 0 1 32 32c0 24-32 64-32 64S0 56 0 32A32 32 0 0 1 32 0z" fill="#3a94c9"/><circle cx="32" cy="32" r="22" fill="#fff"/><circle cx="32" cy="32" r="18" fill="#8cc63f"/><path d="M22 25h4l3 10h11l2-7H27" fill="none" stroke="#fff" stroke-width="2.4"/><circle cx="30" cy="39" r="1.8" fill="#fff"/><circle cx="38" cy="39" r="1.8" fill="#fff"/></svg>
      <h4>GO SHOPPING</h4><p>Lorem ipsum dolor sit amet, consectetur adipiscing elit, sed do eiusmod tempor</p><a>READ MORE</a>
    </div>
    <div class="svc" style="left:614px">
      <svg class="shape" width="207" height="297" viewBox="0 0 207 297"><path d="M0 50L70 0h67l70 50v197l-70 50H70L0 247z" fill="#fff"/></svg>
      <svg class="pin" width="64" height="96" viewBox="0 0 64 96"><path d="M32 0a32 32 0 0 1 32 32c0 24-32 64-32 64S0 56 0 32A32 32 0 0 1 32 0z" fill="#3a94c9"/><circle cx="32" cy="32" r="22" fill="#fff"/><circle cx="32" cy="32" r="18" fill="#8cc63f"/><path d="M32 42l-9-9a5 5 0 0 1 9-6 5 5 0 0 1 9 6z" fill="#fff"/></svg>
      <h4>ENJOY THE POOL</h4><p>Lorem ipsum dolor sit amet, consectetur adipiscing elit, sed do eiusmod tempor</p><a>READ MORE</a>
    </div>
    <div class="svc" style="left:849px">
      <svg class="shape" width="207" height="297" viewBox="0 0 207 297"><path d="M0 50L70 0h67l70 50v197l-70 50H70L0 247z" fill="#fff"/></svg>
      <svg class="pin" width="64" height="96" viewBox="0 0 64 96"><path d="M32 0a32 32 0 0 1 32 32c0 24-32 64-32 64S0 56 0 32A32 32 0 0 1 32 0z" fill="#3a94c9"/><circle cx="32" cy="32" r="22" fill="#fff"/><circle cx="32" cy="32" r="18" fill="#8cc63f"/><rect x="20" y="27" width="24" height="11" rx="5.5" fill="#fff"/><path d="M25 30v5M22.5 32.5h5" stroke="#8cc63f" stroke-width="1.6"/><circle cx="38" cy="31" r="1.4" fill="#8cc63f"/><circle cx="40" cy="34" r="1.4" fill="#8cc63f"/></svg>
      <h4>AQUATIC SPORT</h4><p>Lorem ipsum dolor sit amet, consectetur adipiscing elit, sed do eiusmod tempor</p><a>READ MORE</a>
    </div>
  </section>

  <!-- about -->
  <section>
    <div class="abs about"></div>
    <svg class="abs" style="left:0;top:2673px" width="640" height="455" viewBox="0 0 640 455" role="img" aria-label="Still from the promotional video: villa garden with a private pool at dusk">
      <defs><linearGradient id="poolGrad" x1="0" y1="0" x2="0" y2="1"><stop offset="0" stop-color="#5a5a3a"/><stop offset=".35" stop-color="#4a6a3a"/><stop offset=".55" stop-color="#2a9fd0"/><stop offset="1" stop-color="#1e7fb8"/></linearGradient></defs>
      <polygon points="0,0 575,0 638,455 0,455" fill="url(#poolGrad)"/>
    </svg>
    <div class="abs" style="left:265px;top:2852px;width:92px;height:92px;border-radius:50%;border:5px solid #fff;display:flex;align-items:center;justify-content:center">
      <svg width="30" height="34" viewBox="0 0 30 34"><path d="M4 2l24 15L4 32z" fill="#fff"/></svg></div>
    <div class="abs" style="left:562px;top:2862px;width:76px;height:76px;border-radius:50%;background:#fff;display:flex;align-items:center;justify-content:center"><i style="width:36px;height:36px;border-radius:50%;background:var(--green-dark);display:block"></i></div>
    <h2 class="abs about-title"><b>ABOUT</b> <span>AMBER AND SLATE</span></h2>
    <div class="rule" style="left:678px;top:2784px"></div>
    <p class="abs about-copy">Lorem ipsum dolor sit amet, consectetur adipiscing elit, sed do eiusmod tempor incididunt ut labore et dolore magna aliqua. Ut enim ad minim veniam, quis nostrud exercitation ullamco laboris nisi ut aliquip ex ea commodo consequat. Duis aute irure dolor in reprehenderit in voluptate velit esse cillum dolore eu fugiat null</p>
    <div class="btn btn-green" style="left:678px;top:3020px;width:155px;height:38px;font-size:15px;font-weight:500;gap:8px">Read more
      <svg width="14" height="14" viewBox="0 0 14 14"><circle cx="7" cy="7" r="7" fill="#fff"/><path d="M5.5 4l3 3-3 3" fill="none" stroke="#8cc63f" stroke-width="2"/></svg></div>
  </section>

  <!-- blog -->
  <section>
    <h2 class="abs center sec-title" style="top:3221px"><b>BLOG</b> <span>POSTS</span></h2>
    <div class="rule" style="top:3267px"></div>
    <article class="post" style="left:144px">
      <div class="ph" role="img" aria-label="Photo of friends jumping off a wooden sailing boat" style="background:linear-gradient(180deg,#e8dcc6 0%,#c9a57c 40%,#b07a48 75%,#8a5a30 100%)"></div>
      <div class="box">
        <h3>SED UT PERSPICIATIS UNDE OMNIS</h3>
        <div class="meta"><span><i></i>by Lena Ortis</span>|<span><i style="background:#3a94c9"></i>Apr 25, 2018 at 3:13 pm</span></div>
        <p class="txt">Sed ut perspiciatis unde omnis iste natus error sit voluptatem accusantium doloremque laudantium, totam quasi architecto beatae vitae dicta sunt explicabo.</p>
        <div class="btn btn-blue">Read more</div>
      </div>
    </article>
    <article class="post" style="left:621px">
      <div class="ph" role="img" aria-label="Underwater photo of a green Posidonia seagrass meadow" style="background:linear-gradient(180deg,#1f7fc2 0%,#2a9fd4 35%,#3c8a3a 65%,#2c6a28 100%)"></div>
      <div class="box">
        <h3>SED UT PERSPICIATIS UNDE OMNIS</h3>
        <div class="meta"><span><i></i>by Lena Ortis</span>|<span><i style="background:#3a94c9"></i>Apr 25, 2018 at 3:13 pm</span></div>
        <p class="txt">Sed ut perspiciatis unde omnis iste natus error sit voluptatem accusantium doloremque laudantium, totam quasi architecto beatae vitae dicta sunt explicabo.</p>
        <div class="btn btn-blue">Read more</div>
      </div>
    </article>
  </section>

  <!-- footer -->
  <footer>
    <svg class="abs footer" width="1200" height="376" viewBox="0 0 1200 376">
      <polygon points="0,56 0,122 170,122" fill="#8cc63f"/>
      <polygon points="170,122 1200,22 1200,34 185,122" fill="#8cc63f"/>
      <polygon points="0,122 1200,30 1200,376 0,376" fill="#1f1f1f"/>
      <polygon points="0,115 170,122 0,122" fill="#8cc63f"/>
    </svg>
    <div class="abs" style="left:563px;top:3882px;width:74px;height:74px;border-radius:50%;background:#fff;display:flex;align-items:center;justify-content:center"><i style="width:34px;height:34px;border-radius:50%;background:var(--green-dark);display:block"></i></div>
    <div class="abs social">
      <span></span><span></span><span></span><span></span><span></span>
      <span><svg width="18" height="13" viewBox="0 0 18 13"><rect width="18" height="13" rx="1.5" fill="#fff"/><path d="M1 1l8 6 8-6" fill="none" stroke="#1f1f1f" stroke-width="1.5"/></svg></span>
    </div>
    <div class="abs center f-contact">
      <span><svg width="9" height="12" viewBox="0 0 9 12"><path d="M4.5 0A4.5 4.5 0 0 1 9 4.5C9 8 4.5 12 4.5 12S0 8 0 4.5A4.5 4.5 0 0 1 4.5 0z" fill="#fff"/></svg> 135,Sed ut perspiciatis unde omniatus</span><span>|</span>
      <span><svg width="11" height="11" viewBox="0 0 24 24"><path fill="#fff" d="M6.6 10.8a15 15 0 0 0 6.6 6.6l2.2-2.2c.3-.3.7-.4 1-.2 1.1.4 2.3.6 3.6.6.6 0 1 .4 1 1V20c0 .6-.4 1-1 1A17 17 0 0 1 3 4c0-.6.4-1 1-1h3.5c.6 0 1 .4 1 1 0 1.3.2 2.5.6 3.6.1.3 0 .7-.2 1z"/></svg> Phone : 1 888 888 8888</span><span>|</span>
      <span><svg width="12" height="9" viewBox="0 0 18 13"><rect width="18" height="13" rx="1.5" fill="#fff"/><path d="M1 1l8 6 8-6" fill="none" stroke="#1f1f1f" stroke-width="1.5"/></svg> info@amberandslate.example</span>
    </div>
    <nav class="abs center f-nav">HOME &nbsp;/&nbsp; EXPERIENCE &nbsp;/&nbsp; ABOUT US &nbsp;/&nbsp; CONTACT US</nav>
    <p class="abs center f-copy">© 2019 Amberandslate.All Rights Reserved</p>
  </footer>

</div>
</body>
</html>
```